PlumVesta screens tidy up

We would like advice on how to better present the following home page and overview pages.

The existing website is functional, but the pages don't appear professionals and pleasing to the eye. We would specifically like feedback on alignment and padding of icons and text to make the screen more appealing and polished.

We are following the quartzline design system.

1 page

Sans Serif
• IBM Plex, Poppins

```html
<!DOCTYPE html>
<html lang="en">
<head>
<meta charset="utf-8">
<title>PlumVesta screens</title>
<link rel="stylesheet" href="https://fonts.googleapis.com/css2?family=IBM+Plex+Sans:wght@400;500;600;700&display=swap">
<style>
:root{
  --backdrop:#c9a377;
  --shell:#ffffff;
  --header:#2e2e2e;
  --ink:#1f1f1f;
  --muted:#6b6b6b;
  --line:#e2e2e2;
  --soft:#f4f4f4;
  --accent:#ee7b1f;
  --active:#3a3a3a;
}
*{box-sizing:border-box;margin:0;padding:0}
html,body{width:851px;height:1200px;overflow:hidden}
body{background:var(--backdrop);font-family:"IBM Plex Sans",Arial,sans-serif;color:var(--ink);position:relative}
.screen{position:absolute;left:20px;width:812px;background:var(--shell);display:flex;flex-direction:column;box-shadow:0 2px 6px rgba(0,0,0,.15)}
.screen--overview{top:20px;height:468px}
.screen--home{top:511px;height:653px}
.topbar{height:57px;background:var(--header);display:flex;align-items:center;color:#fff;flex-shrink:0}
.brand{width:122px;height:100%;display:flex;align-items:center;gap:6px;padding-left:12px;font-weight:700;font-size:14px;background:#252525}
.brand-dot{width:12px;height:12px;background:var(--accent);border-radius:50%}
.page-title{flex:1;padding-left:16px}
.page-title small{display:block;font-size:9px;color:#cfcfcf}
.page-title h1{font-size:19px;font-weight:500}
.user{display:flex;align-items:center;gap:6px;padding-right:16px;font-size:8px}
.user-avatar{width:14px;height:14px;border-radius:50%;background:var(--accent)}
.body{flex:1;display:flex;min-height:0}
.sidenav{width:122px;border-right:1px solid var(--line);padding-top:8px;font-size:8px;flex-shrink:0}
.nav-item{display:flex;align-items:center;gap:6px;height:17px;padding:0 10px;color:#444}
.nav-item::before{content:"";width:5px;height:5px;border:1px solid #999;border-radius:1px}
.nav-group{font-size:9px;font-weight:600;padding:6px 10px 2px;color:var(--ink)}
.nav-item.is-active{background:var(--active);color:#fff}
.nav-item.is-active::before{border-color:#fff}
.nav-item.is-current{color:var(--accent);background:#fdeee2;font-weight:600}
.nav-item.is-current::before{border-color:var(--accent)}
.nav-item.sub{padding-left:18px}
.content{flex:1;padding:10px 16px;display:flex;flex-direction:column;gap:6px}
.section-title{font-size:10px;font-weight:600;margin-top:4px}
.card{border:1px solid var(--line);border-radius:3px;padding:8px 12px;background:#fff}
.card-title{color:var(--accent);font-weight:600;font-size:11px;display:flex;align-items:center;gap:6px}
.card-text{font-size:7.5px;color:var(--muted);margin-top:3px}
.icon{width:12px;height:12px;flex-shrink:0}
.row{display:flex;gap:12px}
.row>*{flex:1}
.stats{display:flex;gap:22px;margin-top:8px;font-size:14px;font-weight:600;align-items:center}
.stats span{display:flex;align-items:center;gap:5px}
.campaign-card{display:flex;align-items:center;justify-content:space-between;height:40px}
.btn-ghost{font-size:7px;background:#d8d8d8;color:#666;padding:3px 8px;border-radius:8px}
.split{display:flex;gap:12px}
.split>div{flex:1;display:flex;flex-direction:column;gap:6px}
.section-head{display:flex;justify-content:space-between;align-items:center;margin-top:6px}
.btn-dark{background:var(--header);color:#fff;font-size:7.5px;padding:4px 10px;border-radius:10px}
.tile{background:var(--soft);border:1px solid var(--line);border-radius:4px;padding:10px 14px;text-align:center;height:160px}
.tile-title{color:var(--accent);font-size:11px;font-weight:600}
.tile-text{font-size:8px;color:var(--muted);margin-top:2px}
.tile-stat{display:flex;justify-content:center;align-items:center;gap:8px;margin-top:30px}
.tile-stat b{font-size:34px;font-weight:600;line-height:1}
.tile-stat div{text-align:left;font-size:8px;font-weight:600}
.tile-stat em{display:block;font-style:normal;color:var(--accent);font-size:7px;font-weight:500}
.tile-foot{font-size:6.5px;color:#999;margin-top:8px}
</style>
</head>
<body>
<svg width="0" height="0" style="position:absolute">
  <symbol id="i-block" viewBox="0 0 12 12"><circle cx="6" cy="6" r="4.8" fill="none" stroke="#333" stroke-width="1.3"/><line x1="2.6" y1="9.4" x2="9.4" y2="2.6" stroke="#333" stroke-width="1.3"/></symbol>
  <symbol id="i-file" viewBox="0 0 12 12"><path d="M2.5 1h5l2.5 2.5V11h-7.5z" fill="none" stroke="#333" stroke-width="1.2"/></symbol>
  <symbol id="i-org" viewBox="0 0 12 12"><rect x="1.5" y="2" width="9" height="9" fill="none" stroke="#333" stroke-width="1.2"/><line x1="4" y1="5" x2="8" y2="5" stroke="#333"/><line x1="4" y1="8" x2="8" y2="8" stroke="#333"/></symbol>
  <symbol id="i-info" viewBox="0 0 12 12"><circle cx="6" cy="6" r="5" fill="none" stroke="#333" stroke-width="1.1"/><line x1="6" y1="5" x2="6" y2="9" stroke="#333" stroke-width="1.3"/><circle cx="6" cy="3.3" r=".8" fill="#333"/></symbol>
  <symbol id="i-dot" viewBox="0 0 12 12"><circle cx="6" cy="6" r="5.5" fill="#ee7b1f"/><circle cx="6" cy="6" r="2" fill="#fff"/></symbol>
</svg>

<section class="screen screen--overview">
  <header class="topbar">
    <div class="brand"><span class="brand-dot"></span>PlumVesta</div>
    <div class="page-title"><small>My Custom Campaign</small><h1>Overview</h1></div>
    <div class="user"><span class="user-avatar"></span>Dana Morrow</div>
  </header>
  <div class="body">
    <nav class="sidenav">
      <div class="nav-item">Home</div>
      <div class="nav-item">All Alerts</div>
      <div class="nav-item">Manage</div>
      <div class="nav-group">Campaigns</div>
      <div class="nav-item is-active">My Custom Campaign</div>
      <div class="nav-item sub is-current">Overview</div>
      <div class="nav-item sub">Files &amp; HoneyTokens</div>
      <div class="nav-item sub">Resources</div>
      <div class="nav-item sub">Alerts</div>
      <div class="nav-item sub">Settings</div>
      <div class="nav-item">Default campaign</div>
    </nav>
    <main class="content">
      <h2 class="section-title">Campaign</h2>
      <div class="card campaign-card">
        <div>
          <div class="card-title"><svg class="icon"><use href="#i-dot"/></svg>My custom campaign</div>
          <div class="card-text" style="padding-left:18px">This is my campaign for finding i</div>
        </div>
        <span class="btn-ghost">Disable</span>
      </div>
      <h2 class="section-title">Campaign organisation</h2>
      <div class="row">
        <div class="card">
          <div class="card-title"><svg class="icon"><use href="#i-org"/></svg>Self-enabling Deliverables Proprietary Limited Standard</div>
          <div class="card-text">Standard</div>
          <div class="stats"><span><svg class="icon"><use href="#i-block"/></svg>0</span></div>
        </div>
        <div class="card">
          <div class="card-title">Unleash bleeding-edge mindshare</div>
          <div class="card-text">8 hours ago</div>
          <div class="stats"><span><svg class="icon"><use href="#i-file"/></svg>30</span></div>
        </div>
      </div>
      <div class="split">
        <div>
          <h2 class="section-title">Files &amp; HoneyTokens</h2>
          <div class="card" style="height:62px">
            <div class="card-title"><svg class="icon"><use href="#i-file"/></svg>Statistics</div>
            <div class="stats"><span><svg class="icon"><use href="#i-block"/></svg>0</span><span><svg class="icon"><use href="#i-file"/></svg>30</span></div>
          </div>
        </div>
        <div>
          <h2 class="section-title">Resources</h2>
          <div class="card" style="height:62px">
            <svg class="icon"><use href="#i-org"/></svg>
            <div class="card-text">Generate a collection of fictional organisations. Custom templates. Uploaded files and logos</div>
          </div>
        </div>
      </div>
      <h2 class="section-title">Alerts</h2>
      <div class="card" style="width:50%;height:60px">
        <svg class="icon"><use href="#i-info"/></svg>
        <div class="card-text">Alert statistics will appear here</div>
      </div>
    </main>
  </div>
</section>

<section class="screen screen--home">
  <header class="topbar">
    <div class="brand"><span class="brand-dot"></span>PlumVesta</div>
    <div class="page-title"><h1>Home</h1></div>
    <div class="user"><span class="user-avatar"></span>Dana Morrow</div>
  </header>
  <div class="body">
    <nav class="sidenav">
      <div class="nav-item is-active">Home</div>
      <div class="nav-item">All Alerts</div>
      <div class="nav-item">Manage</div>
      <div class="nav-group">Campaigns</div>
      <div class="nav-item">My Custom Campaign</div>
      <div class="nav-item sub">Overview</div>
      <div class="nav-item sub">Files &amp; HoneyTokens</div>
      <div class="nav-item sub">Resources</div>
      <div class="nav-item sub">Alerts</div>
      <div class="nav-item sub">Settings</div>
      <div class="nav-item">Default campaign</div>
    </nav>
    <main class="content">
      <h2 class="section-title">Teamspace</h2>
      <div class="card">
        <div class="card-title">Default</div>
        <div class="card-text">The default client is created as a part of your user account.</div>
      </div>
      <div class="split">
        <div>
          <h2 class="section-title">Subscription Overview</h2>
          <div class="card" style="height:56px">
            <div class="card-title"><svg class="icon"><use href="#i-file"/></svg>Starter pack usage</div>
            <div class="card-text">4 files active out of 10 allowed</div>
          </div>
        </div>
        <div>
          <h2 class="section-title">Files and Honey Tokens</h2>
          <div class="card" style="height:56px">
            <div class="card-title"><svg class="icon"><use href="#i-file"/></svg>Statistics</div>
            <div class="stats"><span><svg class="icon"><use href="#i-block"/></svg>0</span><span><svg class="icon"><use href="#i-file"/></svg>30</span></div>
          </div>
        </div>
      </div>
      <div class="section-head">
        <h2 class="section-title" style="margin:0">Teamspace</h2>
        <span class="btn-dark">New Campaign +</span>
      </div>
      <div class="row">
        <div class="tile">
          <div class="tile-title">My custom campaign</div>
          <div class="tile-text">This is my custom campaign for finding</div>
          <div class="tile-stat"><b>0</b><div><em>Active</em>Files &amp; Honey Tokens</div></div>
          <div class="tile-foot">Active since Jan 12 2024</div>
        </div>
        <div class="tile">
          <div class="tile-title">Default campaign</div>
          <div class="tile-text">Define your own mission, or combine different.</div>
          <div class="tile-stat"><b>0</b><div><em>Active</em>Files &amp; Honey Tokens</div></div>
          <div class="tile-foot">Active since Jan 12 2024</div>
        </div>
      </div>
    </main>
  </div>
</section>
</body>
</html>
```